Founder / concept developer needs business card // Consultant needs VCARD

I need a business card for me as a founding consultant in Berlin. I advise entrepreneurs, especially in the design of business ideas, business plans or financing applications. More information about this in the annexes. My USP: I design / structure complex ideas and projects convincingly so that my client is successful. I want to communicate professionalism, effectiveness and clarity. Colors like from the range BLACK-GRAY-GREEN. I am 27 years old, I have studied business for 7 years. Attachments: - Business card design (only idea, do not focus on it) - Website screenshot (only idea, do not focus on it)

Target Market(s)

Target group: Founder (20-50 yrs, m / w, needy, in "break-up phase") and CONTRACTOR / "financier" (30-55 yrs, m / w, often public service "routine-oriented"). The foundations are in quite different industries: digital, craft, tourism, retail, services, etc. Almost all German.

Industry/Entity Type

Consultant

Contact Information for Business Card

Lukas Brennwald
M. Sc., International Business Administration
Gründungsberater, Konzeptentwickler
www.kelvoran-mitrel.de
Postfach-Zugang@kelvoran.de
Tel. 0481 294 3172

Colors

Designer to choose colors to be used in the design.

Requirements
Must have
• Professionalism, persuasiveness, clarity
Nice to have
• memorability
Should not have
• Schnörkelei

```html
<!DOCTYPE html>
<html lang="de">
<head>
<meta charset="utf-8">
<title>Lukas Brennwald – Visitenkarte</title>
<link rel="stylesheet" href="https://fonts.googleapis.com/css2?family=Arimo:wght@400;700&display=swap">
<style>
  :root {
    --bg: #e4e5e8;
    --paper: #f7f7f5;
    --ink: #2a2e37;
    --ink-soft: #3a3f49;
    --navy: #2b303b;
    --on-navy: #eef0f3;
  }
  * { box-sizing: border-box; margin: 0; padding: 0; }
  html, body { width: 1200px; height: 800px; overflow: hidden; }
  body {
    background: var(--bg);
    font-family: "Arimo", Arial, sans-serif;
    color: var(--ink);
    position: relative;
  }
  .card {
    position: absolute;
    top: 241px;
    width: 530px;
    height: 318px;
    box-shadow: 0 10px 30px rgba(20, 24, 32, 0.18);
  }
  .card--front { left: 50px; background: var(--paper); }
  .card--back  { left: 620px; background: var(--navy); }

  /* front */
  .brand-mark {
    position: absolute;
    top: 28px;
    right: 30px;
    display: flex;
    align-items: center;
    gap: 10px;
  }
  .brand-mark__square { width: 40px; height: 40px; background: var(--ink); }
  .brand-mark__name { font-weight: 700; font-size: 17px; color: var(--ink); }

  .identity {
    position: absolute;
    right: 30px;
    top: 176px;
    text-align: right;
  }
  .identity__name {
    font-weight: 700;
    font-size: 23px;
    letter-spacing: 0.3px;
    text-transform: uppercase;
    margin-bottom: 6px;
  }
  .identity__role {
    font-size: 13.5px;
    line-height: 1.3;
    color: var(--ink-soft);
  }

  .contact {
    position: absolute;
    left: 30px;
    bottom: 28px;
    list-style: none;
  }
  .contact__item {
    display: flex;
    align-items: center;
    gap: 10px;
    font-size: 15px;
    line-height: 24px;
    color: var(--ink);
  }
  .contact__icon { width: 16px; height: 16px; flex: none; }

  /* back */
  .back-mark {
    position: absolute;
    left: 50%;
    top: 96px;
    transform: translateX(-50%);
    display: flex;
    align-items: center;
    gap: 14px;
  }
  .back-mark__square { width: 72px; height: 72px; background: var(--on-navy); }
  .back-mark__name { font-weight: 700; font-size: 26px; color: var(--on-navy); }

  .back-url {
    position: absolute;
    left: 0;
    right: 0;
    bottom: 54px;
    text-align: center;
    font-size: 13px;
    letter-spacing: 6px;
    color: var(--on-navy);
  }
</style>
</head>
<body>

<section class="card card--front" aria-label="Vorderseite">
  <div class="brand-mark">
    <span class="brand-mark__square"></span>
    <span class="brand-mark__name">Brennwald</span>
  </div>

  <div class="identity">
    <h1 class="identity__name">Lukas Brennwald</h1>
    <p class="identity__role">M. Sc., International Business Administration</p>
    <p class="identity__role">Gründungsberater, Konzeptentwickler</p>
  </div>

  <ul class="contact">
    <li class="contact__item">
      <svg class="contact__icon" viewBox="0 0 16 16" aria-hidden="true">
        <path fill="#2a2e37" d="M4.2 1.2 6.3 4 5 5.6c.8 1.9 2.2 3.4 4.2 4.3l1.5-1.3 2.9 2-.9 2.6c-.3.6-1 .9-1.7.7C6.3 12.5 3.4 9.6 2 4.9c-.2-.7.1-1.4.7-1.7z"/>
      </svg>
      0481 294 3172
    </li>
    <li class="contact__item">
      <svg class="contact__icon" viewBox="0 0 16 16" aria-hidden="true">
        <rect x="1" y="3" width="14" height="10" fill="#2a2e37"/>
        <path d="M1.5 3.5 8 9l6.5-5.5" fill="none" stroke="#f7f7f5" stroke-width="1.2"/>
      </svg>
      Postfach-Zugang@kelvoran.de
    </li>
    <li class="contact__item">
      <svg class="contact__icon" viewBox="0 0 16 16" aria-hidden="true">
        <g fill="none" stroke="#2a2e37" stroke-width="1.1">
          <circle cx="8" cy="8" r="6.5"/>
          <ellipse cx="8" cy="8" rx="3" ry="6.5"/>
          <path d="M1.5 8h13M2.5 4.8h11M2.5 11.2h11"/>
        </g>
      </svg>
      www.kelvoran-mitrel.de
    </li>
  </ul>
</section>

<section class="card card--back" aria-label="Rückseite">
  <div class="back-mark">
    <span class="back-mark__square"></span>
    <span class="back-mark__name">Brennwald</span>
  </div>
  <p class="back-url">www.kelvoran-mitrel.de</p>
</section>

</body>
</html>
```